Zolvana Stationary and Branding Documents

Corporate Identity Branding stationary needed for IT Recruiting Firm.

I already have a Logo, business cards and website. I need to get designs completed for the remaining corporate identity documents.

The documentation should use similar colors as my website and business card. The designs should modern and clean.

http://zolvanaworks.example/

Target Market(s)

Information Technology Industry

Industry/Entity Type

Information Technology

Colors
3377b5
0255a3
fbee3e
f78f20
f37122
33a6d7
000000
0592cd

Requirements
Must have
• Letter Head
• Folder Design
• PowerPoint Design
• Invoice
• Envelope
Nice to have
• Proposal
• Flyer
• Brochure
Should not have
• Logo
• Business Cards
• Website

```html
<!DOCTYPE html>
<html lang="en">
<head>
<meta charset="utf-8">
<title>Zolvana Letterhead</title>
<link href="https://fonts.googleapis.com/css2?family=Open+Sans:wght@400;600&display=swap" rel="stylesheet">
<style>
  :root {
    --backdrop: #e4e5e7;
    --paper: #ffffff;
    --brand-blue: #0f5aa0;
    --band-grey: #58595b;
    --footer-text: #ffffff;
  }
  * { margin: 0; padding: 0; box-sizing: border-box; }
  html, body {
    width: 1066px;
    height: 1200px;
    overflow: hidden;
    background: var(--backdrop);
    font-family: "Open Sans", sans-serif;
  }
  .letterhead {
    position: absolute;
    left: 133px;
    top: 34px;
    width: 800px;
    height: 1132px;
    background: var(--paper);
    box-shadow: 0 6px 24px rgba(0, 0, 0, 0.12);
    overflow: hidden;
  }
  .brand {
    position: absolute;
    left: 76px;
    top: 76px;
  }
  .brand-name {
    font-size: 40px;
    font-weight: 400;
    color: var(--band-grey);
    line-height: 1;
  }
  .footer-bands {
    position: absolute;
    left: 0;
    top: 1000px;
    width: 800px;
    height: 80px;
  }
  .contact {
    position: absolute;
    top: 1014px;
    display: flex;
    flex-direction: column;
    gap: 4px;
    color: var(--footer-text);
    font-size: 12.5px;
    line-height: 1.35;
    font-style: normal;
  }
  .contact-address { left: 470px; }
  .contact-lines { left: 600px; }
  .contact-item { display: flex; align-items: center; gap: 8px; }
  .contact-item svg { width: 11px; height: 11px; fill: var(--footer-text); }
</style>
</head>
<body>
  <main class="letterhead">
    <header class="brand">
      <span class="brand-name">Zolvana</span>
    </header>

    <svg class="footer-bands" viewBox="0 0 800 80" aria-hidden="true">
      <polygon points="440,0 800,0 800,76 400,76" fill="var(--brand-blue)"/>
      <polygon points="0,24 455,24 425,76 0,76" fill="var(--band-grey)"/>
    </svg>

    <address class="contact contact-address">
      <span>One Harbor Plaza</span>
      <span>410 Linden Avenue</span>
    </address>

    <div class="contact contact-lines">
      <span class="contact-item">
        <svg viewBox="0 0 24 24"><path d="M6.6 10.8a15.1 15.1 0 0 0 6.6 6.6l2.2-2.2a1 1 0 0 1 1-.25 11.4 11.4 0 0 0 3.6.57 1 1 0 0 1 1 1V20a1 1 0 0 1-1 1A17 17 0 0 1 3 4a1 1 0 0 1 1-1h3.5a1 1 0 0 1 1 1c0 1.25.2 2.45.57 3.6a1 1 0 0 1-.25 1z"/></svg>
        8885550142
      </span>
      <span class="contact-item">
        <svg viewBox="0 0 24 24"><path d="M2 5h20v14H2zm2 2v.5l8 5 8-5V7zm0 2.8V17h16V9.8l-8 5z"/></svg>
        info@zolvanaworks.example
      </span>
    </div>
  </main>
</body>
</html>
```